Website for an electrical contractor :)

We are after a web site which can show pictures of our jobs and our capability in a professional, creative and easily understood way.

----- Brightvale Electrical ------

We really want a visually good looking website with three sections

Section one:
'Completed projects'
We have a few pictures of jobs which we've completed and would like to show off with a brief description. (see uploads)

Section two:
'Our capabilities'
Just a list of what services we offer

Section three:
We would like a 'contact us' section which people can send us a short msg and upload a file for plans to be able to send to us. We would need their name, phone number and email details. We would also need a short privacy policy saying 'we do not disclose information to third parties'.
We also want to display our contact number and postal address

Good luck :)

Target Market(s)

Adults 25 years+
Business owners
Builders
Real estate agents

Industry/Entity Type

Electrical

Colors

Designer to choose colors to be used in the design.

Requirements
Must have
• Visually appealing
Easy to understand
In the 'Completed projects' section, must have a list for each project we do i can upload pictures for it.

```html
<!DOCTYPE html>
<html lang="en">
<head>
<meta charset="utf-8">
<title>Brightvale Electrical</title>
<link rel="stylesheet" href="https://fonts.googleapis.com/css2?family=Lato:wght@300;400;700&display=swap">
<style>
:root{
  --red:#d9001b;
  --red-dark:#8a0012;
  --ink:#2b2b2b;
  --muted:#555;
  --line:#d9001b;
  --grey-bg:#e6e6e6;
  --white:#fff;
}
*{box-sizing:border-box;margin:0;padding:0}
html,body{width:1200px;height:2761px;overflow:hidden}
body{position:relative;font-family:'Lato',sans-serif;color:var(--ink);background:var(--white)}
.abs{position:absolute}

/* header */
.site-header{position:absolute;left:0;top:0;width:1200px;height:98px;background:var(--white)}
.brand{position:absolute;left:59px;top:20px;display:flex;align-items:center;gap:12px}
.brand-dot{width:40px;height:40px;border-radius:50%;background:var(--red)}
.brand-name{font-size:42px;font-weight:400;color:#333;line-height:1;letter-spacing:-0.5px}
.brand-tag{position:absolute;left:111px;top:72px;font-size:9px;color:#333}
.main-nav a{position:absolute;top:35px;height:26px;line-height:26px;font-size:14px;color:#555;text-decoration:none;transform:translateX(-50%);white-space:nowrap}
.main-nav a.active{background:var(--red);color:var(--white);width:79px;text-align:center}

/* hero */
.hero{position:absolute;left:0;top:98px;width:1200px;height:611px;background:linear-gradient(180deg,#f1f1f1 0%,#e7e7e7 50%,#f4f4f4 100%)}
.hero-person{position:absolute;left:730px;top:0;width:380px;height:611px;background:linear-gradient(180deg,#e6e6e6 0%,#2e3440 25%,#232831 80%,#5a1a1f 100%);border-radius:180px 180px 0 0}
.hero-title{position:absolute;left:0;width:890px;top:322px;text-align:center;font-size:40px;font-weight:300;color:#333}
.hero-sub{position:absolute;left:0;width:890px;top:374px;text-align:center;font-size:30px;font-weight:300;color:#333}
.hero-text{position:absolute;left:195px;width:500px;top:424px;text-align:center;font-size:13px;line-height:17px;color:#333}
.btn-portfolio{position:absolute;left:339px;top:490px;width:219px;height:46px;background:var(--red);color:var(--white);font-size:18px;display:flex;align-items:center;justify-content:center;gap:18px;border-radius:2px}
.hero-arrow{position:absolute;top:368px}

/* section titles */
.section-title{position:absolute;left:0;width:1200px;text-align:center;font-weight:300;font-size:35px;color:#333}
.title-rule{position:absolute;height:2px;background:var(--line)}

/* projects */
.filters{position:absolute;top:837px;left:455px;display:flex;gap:6px}
.filter{height:28px;line-height:26px;padding:0 8px;font-size:12px;border:1px solid #ccc;color:#333;background:var(--white)}
.filter.active{background:#e3e3e3;width:44px;text-align:center;padding:0}
.project{position:absolute;width:276px}
.project-photo{width:276px;height:147px}
.project-name{margin-top:26px;text-align:center;font-weight:700;font-size:15px;color:#222}
.project-type{margin-top:6px;text-align:center;font-size:12.5px;color:#333}
.ph-dark{background:linear-gradient(135deg,#2a2a2a,#151515)}
.ph-cyan{background:linear-gradient(135deg,#3a7c8c,#7fc6d1 50%,#2b5560)}
.ph-mic{background:linear-gradient(135deg,#c9ccd2,#6d7380 60%,#2f3440)}
.ph-wires{background:linear-gradient(135deg,#1e1e1e,#b49a45 50%,#2a2a2a)}
.ph-board{background:linear-gradient(135deg,#1c3f8f,#4f86d6 55%,#c7d7ea)}
.ph-pylon{background:linear-gradient(180deg,#8aa3a6,#3d5257 70%,#1d2a2d)}

/* capabilities */
.capabilities{position:absolute;left:0;top:1419px;width:1200px;height:694px;background:var(--grey-bg)}
.cap-card{position:absolute;top:147px;width:524px;height:495px;background:var(--white)}
.cap-tab{position:absolute;top:-47px;left:50%;margin-left:-57px;width:114px;height:114px;border-radius:50%;background:var(--white);display:flex;align-items:flex-start;justify-content:center;padding-top:30px}
.cap-heading{position:absolute;top:45px;left:0;width:100%;text-align:center;font-size:35px;font-weight:300;color:#333}
.cap-list{position:absolute;top:124px;list-style:none}
.cap-list li{position:relative;height:31.5px;font-size:12.5px;color:#222;padding-left:20px;white-space:nowrap}
.cap-list li::before{content:"";position:absolute;left:0;top:5px;width:7px;height:7px;border-radius:50%;background:var(--red)}

/* contact */
.contact{position:absolute;left:0;top:2113px;width:1200px;height:648px;background:var(--red);color:var(--white)}
.contact .section-title{color:var(--white)}
.contact .title-rule{background:var(--white)}
.field{position:absolute;background:var(--white);color:#555;font-size:15px;padding:0 20px;display:flex;align-items:center;border-radius:2px}
.field.textarea{align-items:flex-start;padding-top:16px}
.btn-send{position:absolute;left:132px;top:482px;width:155px;height:49px;background:var(--red-dark);color:var(--white);font-size:15px;display:flex;align-items:center;justify-content:center}
.privacy-note{position:absolute;right:495px;top:483px;font-size:12.5px}
.info-head{position:absolute;left:738px;top:162px;font-size:16px;font-weight:700}
.info-text{position:absolute;left:738px;top:196px;width:380px;font-size:15px;line-height:24px}
.info-row{position:absolute;left:742px;display:flex;align-items:center;gap:20px;font-size:15px}
.info-row svg{width:26px;flex:none}
.site-footer{position:absolute;left:59px;top:602px;font-size:16px}
.site-footer a{color:var(--white);text-decoration:none}
.site-footer a.u{text-decoration:underline}
.social{position:absolute;left:1066px;top:603px;display:flex;gap:14px}
.social span{width:16px;height:16px;border-radius:50%;background:var(--white)}
</style>
</head>
<body>

<header class="site-header">
  <div class="brand"><span class="brand-dot"></span><span class="brand-name">Brightvale</span></div>
  <div class="brand-tag">Electrical &amp; Communications</div>
  <nav class="main-nav">
    <a class="active" style="left:521px" href="#">Home</a>
    <a style="left:622px" href="#">About Us</a>
    <a style="left:729px" href="#">Services</a>
    <a style="left:832px" href="#">Projects</a>
    <a style="left:962px" href="#">Our capabilities</a>
    <a style="left:1101px" href="#">Contact Us</a>
  </nav>
</header>

<section class="hero">
  <div class="hero-person" role="img" aria-label="Smiling electrician in dark work shirt with safety goggles, coiled red cable and tool belt"></div>
  <h1 class="hero-title">Welcome to Our Site</h1>
  <p class="hero-sub">Lorem ipsum dolor sit amit contantry pop</p>
  <p class="hero-text">Donec sit amet tincidunt orci. Proin a mattis felis, et posuere leo. Praesent porta condimentum erat, eu ultricies est scelerisque vitae. Donec et quam ut orci commodo feugiat. Quisque</p>
  <a class="btn-portfolio">View Portflio
    <svg width="10" height="14" viewBox="0 0 10 14"><path d="M2 1l6 6-6 6" fill="none" stroke="#fff" stroke-width="2.5"/></svg></a>
  <svg class="hero-arrow" style="left:28px" width="18" height="30" viewBox="0 0 18 30"><path d="M15 2L3 15l12 13" fill="none" stroke="#888" stroke-width="2.5"/></svg>
  <svg class="hero-arrow" style="left:1154px" width="18" height="30" viewBox="0 0 18 30"><path d="M3 2l12 13L3 28" fill="none" stroke="#888" stroke-width="2.5"/></svg>
</section>

<section class="projects">
  <div class="title-rule" style="left:337px;top:776px;width:96px"></div>
  <h2 class="section-title" style="top:753px">Completed projects</h2>
  <div class="title-rule" style="left:758px;top:776px;width:96px"></div>
  <div class="filters">
    <span class="filter active">All</span>
    <span class="filter">Residential</span>
    <span class="filter">Commercial / Industrial</span>
  </div>

  <div class="project" style="left:162px;top:891px">
    <div class="project-photo ph-dark" role="img" aria-label="Completed residential wiring job, darkened on hover"></div>
    <p class="project-name">Outfield</p><p class="project-type">Residential</p>
  </div>
  <div class="project" style="left:456px;top:891px">
    <div class="project-photo ph-cyan" role="img" aria-label="Patch panel with blue network cabling"></div>
    <p class="project-name">Outfield</p><p class="project-type">Commercial / Industrial</p>
  </div>
  <div class="project" style="left:751px;top:891px">
    <div class="project-photo ph-mic" role="img" aria-label="Microphone in front of a mixing desk"></div>
    <p class="project-name">Outfield</p><p class="project-type">Residential</p>
  </div>
  <div class="project" style="left:162px;top:1152px">
    <div class="project-photo ph-wires" role="img" aria-label="Close-up of wired circuit breakers"></div>
    <p class="project-name">Outfield</p><p class="project-type">Commercial / Industrial</p>
  </div>
  <div class="project" style="left:456px;top:1152px">
    <div class="project-photo ph-board" role="img" aria-label="Blue printed circuit board close-up"></div>
    <p class="project-name">Outfield</p><p class="project-type">Residential</p>
  </div>
  <div class="project" style="left:751px;top:1152px">
    <div class="project-photo ph-pylon" role="img" aria-label="Steel transmission tower against the sky"></div>
    <p class="project-name">Outfield</p><p class="project-type">Commercial / Industrial</p>
  </div>
</section>

<section class="capabilities">
  <div class="title-rule" style="left:337px;top:49px;width:96px"></div>
  <h2 class="section-title" style="top:26px">Our capabilities</h2>
  <div class="title-rule" style="left:758px;top:49px;width:96px"></div>

  <div class="cap-card" style="left:61px">
    <div class="cap-tab"><svg width="30" height="26" viewBox="0 0 30 26"><path d="M15 1L1 13h4v12h7v-8h6v8h7V13h4z" fill="#d9001b"/></svg></div>
    <h3 class="cap-heading">Residential</h3>
    <ul class="cap-list" style="left:30px">
      <li>24hr Support / faults</li><li>RCD (Safety Switch) installations</li><li>Smoke alarms</li><li>Power points</li><li>Lighting points</li><li>External lighting</li><li>Sensor lighting</li><li>Switching</li><li>Antennas and Arial points</li><li>Dimmers</li><li>Ceiling fans</li>
    </ul>
    <ul class="cap-list" style="left:262px">
      <li>Exhaust fans</li><li>Kitchen / Bathroom Projects</li><li>Re-wires</li><li>Smart wiring</li><li>Phone points</li><li>Data points</li><li>Mains/sub mains cabling</li><li>Switchboard installations/relocations</li><li>Compliance investigations/inspections</li><li>Concrete and wall chasing</li><li>Temporary builders site power</li>
    </ul>
  </div>

  <div class="cap-card" style="left:613px">
    <div class="cap-tab"><svg width="22" height="30" viewBox="0 0 22 30"><rect x="1" y="1" width="20" height="28" fill="#d9001b"/><g fill="#fff"><rect x="5" y="5" width="4" height="3"/><rect x="13" y="5" width="4" height="3"/><rect x="5" y="11" width="4" height="3"/><rect x="13" y="11" width="4" height="3"/><rect x="5" y="17" width="4" height="3"/><rect x="13" y="17" width="4" height="3"/><rect x="9" y="23" width="4" height="6"/></g></svg></div>
    <h3 class="cap-heading">Commercial / Industrial</h3>
    <ul class="cap-list" style="left:31px">
      <li>24hr Support / faults</li><li>Lighting/power design and consultation</li><li>Commercial lighting</li><li>Emergency and exit lighting</li><li>Led strip lighting</li><li>Energy efficient lighting</li><li>Temporary lighting</li><li>Illuminated signage</li><li>Switchboard relocations</li><li>Maintenance</li><li>RCD installation</li>
    </ul>
    <ul class="cap-list" style="left:289px">
      <li>Phone/data points</li><li>Data cabinets</li><li>Data Networking</li><li>IDF installations/relocations</li><li>All power requirements</li><li>All three phase power requirements</li><li>Electrical rip outs / Disconnections</li><li>Thermal Imaging scans</li><li>Concrete and wall chasing</li>
    </ul>
  </div>
</section>

<section class="contact">
  <div class="title-rule" style="left:383px;top:77px;width:97px"></div>
  <h2 class="section-title" style="top:54px">contact us</h2>
  <div class="title-rule" style="left:710px;top:77px;width:98px"></div>

  <div class="field" style="left:132px;top:167px;width:280px;height:50px">Name</div>
  <div class="field" style="left:425px;top:167px;width:280px;height:50px">Email</div>
  <div class="field" style="left:132px;top:231px;width:280px;height:52px">Phone</div>
  <div class="field" style="left:425px;top:231px;width:280px;height:52px">Upload Plan</div>
  <div class="field textarea" style="left:132px;top:296px;width:573px;height:169px">Message</div>
  <div class="btn-send">Send Message</div>
  <p class="privacy-note">we do not disclose information to third parties</p>

  <h3 class="info-head">ADDITIONAL INFO</h3>
  <p class="info-text">If you have any questiong about our products or something else, please email us or call us. We'll get in touch with you as soon as possible.</p>
  <div class="info-row" style="top:315px"><svg viewBox="0 0 26 26" height="24"><path d="M13 1a8 8 0 0 0-8 8c0 6 8 16 8 16s8-10 8-16a8 8 0 0 0-8-8zm0 11a3 3 0 1 1 0-6 3 3 0 0 1 0 6z" fill="#fff"/></svg>18 Harlow Street, Brightvale</div>
  <div class="info-row" style="top:359px"><svg viewBox="0 0 26 26" height="22"><path d="M6 2l4 5-2 3c1 3 4 6 7 7l3-2 5 4-2 4C12 23 3 14 2 5z" fill="#fff"/></svg>+61 - 400 555 0192</div>
  <div class="info-row" style="top:399px"><svg viewBox="0 0 26 20" height="20"><rect x="1" y="1" width="24" height="18" rx="2" fill="#fff"/><path d="M2 3l11 8 11-8" fill="none" stroke="#d9001b" stroke-width="2"/></svg>hello@brightvale.example</div>

  <footer class="site-footer">©2015 brightvale - <a href="#">Terms of Service</a> - <a href="#">Privacy</a> - <a class="u" href="#">Contact</a></footer>
  <div class="social"><span></span><span></span><span></span></div>
</section>

</body>
</html>
```